Card Design for my dog training business Brightpaw Obedience

Need a business card design for my dog training business with my new logo. Want the card to come off professional yet fun. Want it to be very eye catchy as well. I normally have these at vet clinics, pet stores, and groomers. so need it to look better than my competitors.
Target Market(s)
dog owners
Industry/Entity Type
Dog Training
Contact Information for Business Card
needs logo, my name and info
Font styles to use
Serif
Colors
0255a3
ffffff
ec1f27
000000
333333
fbfbfb
Requirements
Must have
- Brightpaw Obedience
- Felix Orland
- 415 903 2276
- info@brightpawobedience.example
- www.brightpawobedience.example

```html
<!DOCTYPE html>
<html lang="en">
<head>
<meta charset="UTF-8">
<title>Brightpaw Obedience – Business Card</title>
<link href="https://fonts.googleapis.com/css2?family=Cinzel:wght@400&family=Cormorant+Garamond:ital,wght@0,500;1,400&family=Lato:wght@400&display=swap" rel="stylesheet">
<style>
  :root {
    --backdrop: #161616;
    --card: #262626;
    --card-edge: #303030;
    --silver: #dcdcdc;
    --silver-soft: #a9a9a9;
    --emboss: #3a3a3a;
    --rule: #8a8a8a;
  }
  * { margin: 0; padding: 0; box-sizing: border-box; }
  html, body {
    width: 1200px; height: 900px; overflow: hidden;
    background: var(--backdrop);
  }
  .sheet {
    position: relative; width: 1200px; height: 900px;
    display: flex; flex-direction: column; align-items: center; justify-content: center; gap: 34px;
  }
  .card {
    position: relative; width: 720px; height: 400px;
    background: var(--card);
    border: 1px solid var(--card-edge);
    box-shadow: 0 10px 30px rgba(0,0,0,.5);
  }
  /* Front */
  .card--front { display: flex; align-items: center; justify-content: center; }
  .wordmark {
    font-family: "Cormorant Garamond", serif; font-weight: 500;
    color: var(--silver); font-size: 46px; letter-spacing: 1px;
    display: flex; align-items: center; gap: 16px;
  }
  .wordmark__square {
    width: 18px; height: 18px; background: var(--silver);
  }
  /* Back */
  .card--back { display: flex; }
  .back__brand {
    width: 330px; display: flex; flex-direction: column; align-items: center; justify-content: center; gap: 18px;
  }
  .back__brand .wordmark { color: var(--emboss); font-size: 30px; gap: 10px;
    text-shadow: 0 1px 0 rgba(255,255,255,.06), 0 -1px 0 rgba(0,0,0,.5); }
  .back__brand .wordmark__square { width: 12px; height: 12px; background: var(--emboss); }
  .tagline {
    font-family: "Cormorant Garamond", serif; font-style: italic;
    font-size: 12px; color: var(--emboss);
  }
  .back__rule {
    width: 1px; height: 190px; background: var(--rule); align-self: center;
  }
  .contact {
    padding-left: 70px; align-self: center; color: var(--silver);
    font-family: "Lato", sans-serif;
  }
  .contact__name {
    font-family: "Cinzel", serif; font-size: 20px; letter-spacing: 1.5px;
  }
  .contact__role { font-size: 17px; margin-top: 2px; }
  .contact__address { font-size: 17px; line-height: 1.35; margin-top: 16px; }
  .contact__list { list-style: none; margin-top: 12px; font-size: 17px; line-height: 1.45; }
  .contact__list li { display: flex; align-items: center; gap: 10px; }
  .contact__list svg { width: 13px; height: 13px; flex: none; }
</style>
</head>
<body>
<main class="sheet">
  <section class="card card--front" aria-label="Card front">
    <div class="wordmark"><span class="wordmark__square"></span>Brightpaw Obedience</div>
  </section>

  <section class="card card--back" aria-label="Card back">
    <div class="back__brand">
      <div class="wordmark"><span class="wordmark__square"></span>Brightpaw Obedience</div>
      <p class="tagline">“Training dogs, one happy owner at a time.”</p>
    </div>
    <div class="back__rule"></div>
    <div class="contact">
      <p class="contact__name">FELIX ORLAND</p>
      <p class="contact__role">Managing Director</p>
      <p class="contact__address">58 Alder Lane,<br>Westbrook, NZ, 4021</p>
      <ul class="contact__list">
        <li>
          <svg viewBox="0 0 16 16" fill="none" stroke="currentColor" stroke-width="1.6"><path d="M4 1.5l2.5 3-1.5 1.5a8 8 0 0 0 5 5l1.5-1.5 3 2.5-1.5 2.5C7 14 2 9 1.5 3z"/></svg>
          415 903 2276
        </li>
        <li>
          <svg viewBox="0 0 16 16" fill="none" stroke="currentColor" stroke-width="1.4"><rect x="1.5" y="3.5" width="13" height="9"/><path d="M1.5 3.5L8 9l6.5-5.5"/></svg>
          info@brightpawobedience.example
        </li>
        <li>
          <svg viewBox="0 0 16 16" fill="none" stroke="currentColor" stroke-width="1.3"><circle cx="8" cy="8" r="6.5"/><ellipse cx="8" cy="8" rx="3" ry="6.5"/><path d="M1.5 8h13"/></svg>
          www.brightpawobedience.example
        </li>
      </ul>
    </div>
  </section>
</main>
</body>
</html>
```